We need packaging box design for our solar lights

We need a design for our solar string lights packaging boxes. The final design should communicate an added enjoyment, comfort and beauty when our lights are used to light up warm evening nights in places like backyard, patio restaurant or even family event.

Front and back side of box can be more visual while sides can be used for technical information about the product. There are 2 types of boxes which will have same design - except they need to indicate difference in # of bulbs 10 or 16 . also size of 16 bulb product box is slightly larger so design will need to be slightly adjusted.

Our original logo needs to have "Meadowglow Lamps" text added to it as well.

We put all together in the attachment with some of the examples of photos we like.

Below are more attached files:
1st attachment - general info and samples of photos
Second attachments are photos of our product - they can be adjusted/photoshoped in any way you wish to make the design - or any other acceptable photos you create can be used
Third set of attachments are box templates for 10 and 16 bulbs size box
last are files for logo - choose any you like, edit any colors / text needs to be added/changed to "Meadowglow Lamps " - not go with meadowglow

Target Market(s)

People with yards, patios, restaurants, wedding places... any celebrations or just relaxing during nice warm evening in the beautifully lit place...

Colors

Designer to choose colors to be used in the design.

Requirements
Must have
• indication of bulb numbers
• logo and name Meadowglow lamps
• rest is up to creativity of designer
Nice to have
• some icons

```html
<!DOCTYPE html>
<html lang="en">
<head>
<meta charset="utf-8">
<title>Meadowglow Lamps – Solar String Lights Box</title>
<link rel="stylesheet" href="https://fonts.googleapis.com/css2?family=Oswald:wght@600&family=Roboto+Slab:wght@700&family=Open+Sans:wght@700&display=swap">
<style>
  :root {
    --paper: #ffffff;
    --frame: #333333;
    --flap: #2e2e2e;
    --panel: #050505;
    --orange: #e8772a;
    --copper: #a8683a;
    --gold: #d9c9a0;
    --mist: #8a8a8a;
    --text-light: #ffffff;
    --green: #27a836;
  }
  html, body { margin: 0; padding: 0; overflow: hidden; background: var(--paper); }
  .dieline { display: block; width: 1094px; height: 1200px; }
  .brand-name { font-family: "Oswald", sans-serif; font-weight: 600; fill: var(--gold); letter-spacing: 1px; }
  .brand-sub { font-family: "Roboto Slab", serif; font-weight: 700; fill: var(--text-light); }
  .feature-text { font-family: "Open Sans", sans-serif; font-weight: 700; font-size: 7.2px; fill: var(--orange); }
  .badge-num { font-family: "Oswald", sans-serif; font-weight: 600; fill: var(--text-light); }
  .badge-label { font-family: "Open Sans", sans-serif; font-weight: 700; fill: var(--text-light); }
  .icon-label { font-family: "Open Sans", sans-serif; font-weight: 700; font-size: 3.6px; fill: var(--text-light); }
  .maker-name { font-family: "Open Sans", sans-serif; font-weight: 700; font-size: 4.6px; fill: var(--text-light); letter-spacing: 0.8px; }
</style>
</head>
<body>
<svg class="dieline" viewBox="0 0 848 930" preserveAspectRatio="none" xmlns="http://www.w3.org/2000/svg">
  <defs>
    <linearGradient id="glowBand" x1="0" y1="0" x2="0" y2="1">
      <stop offset="0" stop-color="#3a3220"/>
      <stop offset="0.6" stop-color="#141210"/>
      <stop offset="1" stop-color="#050505"/>
    </linearGradient>
    <linearGradient id="sunsetScene" x1="0" y1="0" x2="0" y2="1">
      <stop offset="0" stop-color="#070605"/>
      <stop offset="0.55" stop-color="#2a1a0c"/>
      <stop offset="0.8" stop-color="#8a5522"/>
      <stop offset="1" stop-color="#2a1a0c"/>
    </linearGradient>
    <radialGradient id="backGlow" cx="0.9" cy="0.35" r="0.6">
      <stop offset="0" stop-color="#3a2410"/>
      <stop offset="1" stop-color="#050505"/>
    </radialGradient>
    <linearGradient id="badgeFill" x1="0" y1="0" x2="0" y2="1">
      <stop offset="0" stop-color="#8a5a2e"/>
      <stop offset="1" stop-color="#4a2c12"/>
    </linearGradient>
  </defs>

  <!-- sheet border -->
  <rect class="sheet-border" x="1" y="1" width="846" height="928" fill="none" stroke="var(--frame)" stroke-width="1.5"/>

  <!-- lid -->
  <g class="lid">
    <path d="M55 58 Q55 18 95 18 H443 Q483 18 483 58 V418 H55 Z" fill="var(--panel)"/>
    <path d="M55 63 H483 V150 H55 Z" fill="url(#glowBand)" role="img" aria-label="Warm bokeh lights glowing across the top"/>
    <g class="lid-waves">
      <path d="M55 345 C160 330 250 385 360 370 C420 360 460 340 483 330 V418 H55 Z" fill="#4a4a4a"/>
      <path d="M55 370 C170 350 260 400 380 385 C430 378 465 360 483 352 V418 H55 Z" fill="var(--copper)"/>
      <path d="M55 392 C180 378 280 412 400 400 C440 396 470 388 483 382 V418 H55 Z" fill="#5a3318"/>
    </g>
    <text class="brand-name" x="258" y="244" font-size="42" text-anchor="middle">MEADOWGLOW</text>
    <text class="brand-sub" x="265" y="281" font-size="30" text-anchor="middle">Lamps</text>
  </g>

  <!-- side glue tab -->
  <rect class="glue-tab" x="10" y="418" width="45" height="266" fill="var(--flap)" stroke="#555" stroke-width="0.6"/>

  <!-- front panel -->
  <g class="front-panel">
    <rect x="55" y="418" width="428" height="266" fill="url(#sunsetScene)" stroke="#555" stroke-width="0.6"/>
    <rect x="255" y="422" width="225" height="258" fill="url(#sunsetScene)" opacity="0.9" role="img" aria-label="String of sixteen glowing bulbs above a solar panel on a ground stake"/>
    <text class="brand-name" x="163" y="474" font-size="32" text-anchor="middle">MEADOWGLOW</text>
    <text class="brand-sub" x="163" y="502" font-size="24" text-anchor="middle">Lamps</text>

    <g class="bulb-badge">
      <rect x="134" y="535" width="56" height="70" rx="10" fill="url(#badgeFill)" stroke="var(--gold)" stroke-width="1.5"/>
      <text class="badge-num" x="162" y="568" font-size="24" text-anchor="middle">16</text>
      <text class="badge-label" x="162" y="579" font-size="7.5" text-anchor="middle">BULBS</text>
      <text class="badge-label" x="162" y="588" font-size="4.5" text-anchor="middle">SOLAR STRING</text>
      <text class="badge-label" x="162" y="595" font-size="4.5" text-anchor="middle">LIGHTS</text>
    </g>

    <g class="feature-icons">
      <circle cx="111" cy="645" r="17" fill="var(--green)"/>
      <circle cx="111" cy="640" r="4" fill="#fff"/>
      <g stroke="#fff" stroke-width="1.2">
        <line x1="111" y1="631" x2="111" y2="633"/><line x1="111" y1="647" x2="111" y2="649"/>
        <line x1="102" y1="640" x2="104" y2="640"/><line x1="118" y1="640" x2="120" y2="640"/>
      </g>
      <text class="icon-label" x="111" y="653" text-anchor="middle">Charges during</text>
      <text class="icon-label" x="111" y="657.5" text-anchor="middle">the day</text>

      <circle cx="158" cy="645" r="17" fill="var(--green)"/>
      <path d="M160 632 A8 8 0 1 0 165 645 A6 6 0 1 1 160 632 Z" fill="#fff"/>
      <text class="icon-label" x="158" y="655" text-anchor="middle">Work at dusk</text>

      <circle cx="204" cy="645" r="17" fill="var(--green)"/>
      <path d="M204 648 V638 M204 641 Q210 632 213 636 Q209 642 204 641" stroke="#fff" stroke-width="1.4" fill="#fff"/>
      <text class="icon-label" x="204" y="655" text-anchor="middle">Green Energy</text>
    </g>
  </g>

  <!-- back panel top flap -->
  <path class="back-flap" d="M490 238 H778 Q792 238 796 252 L838 418 H490 Z" fill="var(--flap)" stroke="#555" stroke-width="0.6"/>

  <!-- back panel -->
  <g class="back-panel">
    <rect x="483" y="418" width="355" height="266" fill="url(#backGlow)" stroke="#555" stroke-width="0.6"/>
    <path d="M483 625 C560 640 620 650 690 630 C760 610 810 620 838 630 V684 H483 Z" fill="#4a4a4a"/>
    <path d="M483 648 C570 660 640 665 710 648 C770 635 815 640 838 648 V684 H483 Z" fill="var(--copper)"/>
    <path d="M483 665 C580 674 660 678 730 666 C780 658 820 662 838 666 V684 H483 Z" fill="#141414"/>

    <g class="feature-list">
      <rect x="526" y="485" width="5" height="5" fill="var(--orange)"/>
      <text class="feature-text" x="538" y="491">16 LED warm white light bulb string</text>
      <rect x="526" y="499" width="5" height="5" fill="var(--orange)"/>
      <text class="feature-text" x="538" y="505">Waterproof connector for easy installation</text>
      <rect x="526" y="513" width="5" height="5" fill="var(--orange)"/>
      <text class="feature-text" x="538" y="519">Total length 29.5 ft / Lighted length 19.7 ft for 16 bulb</text>
      <text class="feature-text" x="538" y="533">product )</text>
      <rect x="526" y="540" width="5" height="5" fill="var(--orange)"/>
      <text class="feature-text" x="538" y="546">Creates pleasant ambient light perfect for Backyard,</text>
      <text class="feature-text" x="538" y="560">Patio, Party, Restaurant Wedding or other scenes</text>
      <rect x="526" y="568" width="5" height="5" fill="var(--orange)"/>
      <text class="feature-text" x="538" y="574">Safe and Convenient: Solar Powered, no need to worry</text>
      <text class="feature-text" x="538" y="588">about the socket location, can be used everywhere</text>
    </g>

    <g class="maker-mark">
      <circle cx="543" cy="641" r="6" fill="var(--orange)"/>
      <text class="maker-name" x="543" y="659" text-anchor="middle">MEADOWGLOW</text>
    </g>
  </g>

  <!-- bottom flaps -->
  <path class="bottom-flap" d="M55 684 H483 V907 H375 V857 H157 V907 H55 Z" fill="var(--flap)" stroke="#555" stroke-width="0.6"/>
  <path class="bottom-flap" d="M490 684 H838 V907 H655 V857 L490 700 Z" fill="var(--flap)" stroke="#555" stroke-width="0.6"/>
</svg>
</body>
</html>
```